New Business card design to reflect rebrand

I would like a business card design with a good base colour for our new logo and also a placeholder for a profile pic of the card holder. the design needs to be editable to the point that we can easily change the picture of the person and use that design for printmerlo etc. we are looking at a metalic finish business card so will need a good base colour to bring out the finish.

Target Market(s)

prospective customers

Industry/Entity Type

Business

Contact Information for Business Card

I would like one editable design that we can change the name of the card holder and profile picture. The design need to be in a format that be send to printmerlo etc.

Our address is Fenwick Lodge, Copse Lane, Ashcombe Vale, GU14 3TP Tel no. 01483 556172

Requirements
Must have
• place holder for a profile pic for the card holder. in AI or preferably PSD format

```html
<!DOCTYPE html>
<html lang="en">
<head>
<meta charset="utf-8">
<title>Brantwell Workplace Services – Business Card</title>
<link rel="stylesheet" href="https://fonts.googleapis.com/css2?family=Open+Sans:wght@400;600;700&display=swap">
<style>
  :root {
    --page-bg: #e9e9e7;
    --card-white: #ffffff;
    --navy: #3e5571;
    --navy-deep: #2f435c;
    --orange: #f07a22;
    --ink-grey: #6f7780;
    --photo-light: #d9d9d9;
    --photo-dark: #b3b3b3;
  }
  * { box-sizing: border-box; margin: 0; padding: 0; }
  html, body { width: 1200px; height: 843px; overflow: hidden; }
  body {
    background: var(--page-bg);
    font-family: "Open Sans", Arial, sans-serif;
    display: flex;
    align-items: center;
    justify-content: center;
    gap: 40px;
  }
  .card {
    width: 560px;
    height: 320px;
    background: var(--card-white);
    box-shadow: 0 6px 18px rgba(0,0,0,.18);
    position: relative;
    overflow: hidden;
  }

  /* Brand name, shared */
  .brand-name {
    display: flex;
    align-items: center;
    gap: 12px;
    font-weight: 700;
    letter-spacing: 1px;
    text-transform: uppercase;
    line-height: 1.2;
  }
  .brand-mark { flex: none; width: 14px; height: 14px; background: var(--orange); }
  .brand-text { display: flex; flex-direction: column; text-align: left; }

  /* Back */
  .card-back {
    display: flex;
    flex-direction: column;
    align-items: center;
    justify-content: center;
    gap: 34px;
  }
  .card-back .brand-name { color: var(--navy); font-size: 24px; }
  .website {
    color: var(--ink-grey);
    font-size: 13px;
    letter-spacing: 5px;
  }

  /* Front */
  .card-front { display: flex; }
  .holder {
    width: 47%;
    display: flex;
    flex-direction: column;
    align-items: center;
    justify-content: center;
  }
  .holder-photo {
    width: 120px;
    height: 140px;
    border-radius: 8px;
    background: linear-gradient(180deg, var(--photo-light), var(--photo-dark));
  }
  .holder-name {
    margin-top: 14px;
    color: var(--navy);
    font-size: 19px;
    font-weight: 600;
  }
  .holder-role {
    color: var(--orange);
    font-size: 14px;
  }
  .company {
    width: 53%;
    padding: 0 20px;
    background: linear-gradient(160deg, var(--navy), var(--navy-deep));
    color: var(--card-white);
    display: flex;
    flex-direction: column;
    align-items: center;
    justify-content: center;
    text-align: center;
  }
  .company .brand-name { font-size: 17px; color: var(--card-white); }
  .address {
    margin-top: 30px;
    font-size: 13px;
    line-height: 1.45;
    font-style: normal;
  }
  .phone {
    margin-top: 14px;
    font-size: 14px;
    display: flex;
    align-items: center;
    gap: 8px;
  }
  .phone svg { width: 13px; height: 13px; fill: var(--orange); }
</style>
</head>
<body>
  <section class="card card-back" aria-label="Card back">
    <div class="brand-name"><span class="brand-mark"></span><span class="brand-text">Brantwell Workplace Services</span></div>
    <div class="website">www.brantwell.co.uk</div>
  </section>

  <section class="card card-front" aria-label="Card front">
    <div class="holder">
      <div class="holder-photo" role="img" aria-label="Profile photo of the card holder"></div>
      <div class="holder-name">Alex Morgan</div>
      <div class="holder-role">CEO/Founder</div>
    </div>
    <div class="company">
      <div class="brand-name">
        <span class="brand-mark"></span>
        <span class="brand-text"><span>Brantwell</span><span>Workplace Services</span></span>
      </div>
      <address class="address">
        Fenwick Lodge<br>
        Copse Lane, Ashcombe Vale<br>
        GU14 3TP
      </address>
      <div class="phone">
        <svg viewBox="0 0 24 24" aria-hidden="true"><path d="M6.6 10.8a15.1 15.1 0 0 0 6.6 6.6l2.2-2.2a1 1 0 0 1 1-.25 11.4 11.4 0 0 0 3.6.57 1 1 0 0 1 1 1V20a1 1 0 0 1-1 1A17 17 0 0 1 3 4a1 1 0 0 1 1-1h3.5a1 1 0 0 1 1 1c0 1.25.2 2.45.57 3.57a1 1 0 0 1-.25 1z"/></svg>
        01483 556172
      </div>
    </div>
  </section>
</body>
</html>
```